Kelvor Engineers: Why you should hire us keepsake

New design. Open to plastic cards. We are an engineering firm that designs cell phone towers and commercial buildings. Please check out our website www.kelvorstruct.com for more details. We want people to remember our card and for it to be useful if possible. We want the same look and feel on these cards to be translated to other marketing material we may need such as brochures.

Target Market(s)

Architects, Developers and Telecommunication Carriers

Industry/Entity Type

Engineering

Contact Information for Business Card

Card with our company colors, logo, and innovative design with elements related to our industry.

Font styles to use
Sans Serif

Colors
9bcb3c
abd036
0255a3

Requirements
Must have
• Sleek and hip design
Nice to have
• Bright lime green and navy coloring that pops with an innovative design.
Should not have
• A basic and boring design

```html
<!DOCTYPE html>
<html lang="en">
<head>
<meta charset="utf-8">
<title>Kelvor Engineers – Business Card</title>
<link href="https://fonts.googleapis.com/css2?family=Source+Sans+3:wght@400;600;800&display=swap" rel="stylesheet">
<style>
  :root {
    --page: #e8edf2;
    --card-top: #f4f7fa;
    --navy: #0f2c5e;
    --navy-ink: #16305f;
    --lime: #2fe034;
    --lime-text: #2dbb2a;
    --name: #b8c5da;
    --contact: #c9d3e3;
  }
  * { box-sizing: border-box; margin: 0; padding: 0; }
  html, body {
    width: 1200px; height: 900px; overflow: hidden;
    background: var(--page);
    font-family: "Source Sans 3", "Myriad Pro", Arial, sans-serif;
  }
  .card {
    position: absolute; left: 120px; top: 177px;
    width: 960px; height: 546px;
    border-radius: 18px; overflow: hidden;
    background: var(--card-top);
    box-shadow: 0 10px 30px rgba(15, 44, 94, .18);
  }
  .brand {
    position: absolute; left: 46px; top: 80px;
    display: flex; align-items: center; gap: 16px;
  }
  .brand-mark {
    width: 34px; height: 34px; background: var(--lime);
  }
  .brand-name {
    font-size: 56px; font-weight: 800; line-height: 1;
    color: var(--lime); letter-spacing: -0.5px;
  }
  .tagline {
    position: absolute; right: 46px; top: 104px;
    font-size: 27px; font-weight: 600; color: var(--navy-ink);
  }
  .divider {
    position: absolute; left: 0; top: 222px; width: 100%; height: 5px;
    background: var(--lime);
  }
  .notch {
    position: absolute; left: 890px; top: 226px;
  }
  .lower {
    position: absolute; left: 0; top: 227px; width: 100%; bottom: 0;
    background: var(--navy);
  }
  .holder {
    position: absolute; right: 46px; top: 41px;
    font-size: 27px; font-weight: 600; color: var(--name);
  }
  .contacts {
    position: absolute; right: 46px; top: 102px;
    list-style: none; text-align: right;
  }
  .contacts li {
    display: flex; justify-content: flex-end; align-items: center; gap: 8px;
    height: 28px; font-size: 20px; color: var(--contact);
  }
  .contacts svg { width: 16px; height: 16px; flex: none; }
  .offices {
    position: absolute; right: 52px; bottom: 38px;
    display: flex; gap: 16px;
    font-size: 21px; color: var(--lime-text); letter-spacing: .3px;
  }
  .offices .sep { color: var(--lime-text); }
</style>
</head>
<body>
  <article class="card">
    <div class="brand">
      <span class="brand-mark"></span>
      <span class="brand-name">Kelvor Engineers</span>
    </div>
    <p class="tagline">Multi-discipline engineering</p>

    <section class="lower">
      <h1 class="holder">Dana Holloway Reyes</h1>
      <ul class="contacts">
        <li>555.014.2231
          <svg viewBox="0 0 16 16"><path d="M3 1.5l3 3-1.6 1.8c.8 1.8 2.5 3.5 4.3 4.3L10.5 9l3 3-2 2.5C6.5 14 2 9.5 1.5 3.5z" fill="#2fe034"/></svg>
        </li>
        <li>555.017.4408
          <svg viewBox="0 0 16 16"><rect x="4" y="1" width="8" height="14" rx="1.5" fill="none" stroke="#2fe034" stroke-width="1.6"/><circle cx="8" cy="12.5" r="1" fill="#2fe034"/></svg>
        </li>
        <li>dreyes@kelvorstruct.com
          <svg viewBox="0 0 16 16"><rect x="1" y="3" width="14" height="10" rx="1" fill="#2fe034"/><path d="M1.5 3.5L8 9l6.5-5.5" fill="none" stroke="#0f2c5e" stroke-width="1.3"/></svg>
        </li>
        <li>www.kelvorstruct.com
          <svg viewBox="0 0 16 16"><circle cx="8" cy="8" r="6.5" fill="#2fe034"/><path d="M1.5 8h13M8 1.5c-3 3.5-3 9.5 0 13M8 1.5c3 3.5 3 9.5 0 13" fill="none" stroke="#0f2c5e" stroke-width="1"/></svg>
        </li>
      </ul>
      <p class="offices">
        <span>BOSTON</span><span class="sep">|</span>
        <span>RICHMOND</span><span class="sep">|</span>
        <span>PHOENIX</span><span class="sep">|</span>
        <span>KANSAS CITY</span>
      </p>
    </section>

    <div class="divider"></div>
    <svg class="notch" width="34" height="20" viewBox="0 0 34 20"><path d="M0 0h34L17 18z" fill="#2fe034"/><path d="M6 1h22L17 12z" fill="#f4f7fa"/></svg>
  </article>
</body>
</html>
```